In-Design Template: Single-sided A3 Brochure

Hi In-Design Experts,

I am after an A3 template which is created using In-Design. It needs to be able to operate in CS3.

This template will be used as the basis for a brochure for a beautiful range of stationery. In order to help me with the layout of the brochure, I require a template to be created using "In-Design". The template that you will create will include Rectangle Frames that will allow me to easily insert my products.

As this template is hard to describe in words, I have attached a diagram of what I am actually after. This is an A3 brochure (created on a slightly bigger canvas). As you will see, the right side is an exact replica of the left side. In creating the brochure, think of beautiful shades of pinks - incorporating baby pinks and pastel pinks - elegant, classy and beautiful.

Further details provided below and in the attached files.

If you require any further information or have any questions, please let me know.

Looking forward to seeing your designs.

Target Market(s)

Women

Requirements
Must have
• Template must be created using "In-Design" and be able to operate in version CS3.
• Template information - In the supporting files, I have set out the following:
• - Size of template (Image A3 created on canvas size SRA3 (450 x 320mm) with crop marks
• - Location of all text areas
• - Location of the boxes for my products - Please use the "Rectangle Frame Tool" to allow me to insert products later on.
• Further Design Work - The template is the basis and I would then require your creativity for the following design work:
• - Text to be included at the top of each page - "Tuvelle" using Edwarian Script (or similar font style. Please use the pink tones described above.
• - Image - I have attached an image that I would like to include in some way. I am thinking of placing this in the corners of the brochure - but opened to ideas. The image is a picture of scattered leaves. The picture I have attached is in shades of purple, however, I would require the leaves in shades of Pink. I am open to how you use these leaves in the template/brochure. You definitely do not need to use the exact leaves as displayed but something similar would be perfect.

```html
<!DOCTYPE html>
<html lang="en">
<head>
<meta charset="utf-8">
<title>Tuvelle Stationery Brochure Template</title>
<link rel="stylesheet" href="https://fonts.googleapis.com/css2?family=Crimson+Pro:wght@400&display=swap">
<style>
  :root {
    --paper: #ffffff;
    --border-pink: #f0c5bc;
    --name-pink: #d99a9a;
    --ink: #404040;
    --frame-grey: #8c8c8c;
    --crop: #111111;
  }
  html, body {
    margin: 0;
    padding: 0;
    width: 1200px;
    height: 880px;
    overflow: hidden;
    background: var(--paper);
  }
  .sheet {
    position: relative;
    width: 1200px;
    height: 880px;
    background: var(--paper);
    font-family: "Crimson Pro", "Times New Roman", serif;
    color: var(--ink);
  }
  .crop-marks {
    position: absolute;
    inset: 0;
  }
  .page-border {
    position: absolute;
    left: 40px;
    top: 44px;
    width: 1121px;
    height: 792px;
    box-sizing: border-box;
    border: 6.5px solid var(--border-pink);
  }
  .leaves {
    position: absolute;
  }
  .leaves-top {
    left: 46px;
    top: 50px;
    width: 1109px;
    height: 80px;
    background: linear-gradient(180deg, rgba(234,176,180,0.55) 0%, rgba(238,195,168,0.25) 55%, rgba(255,255,255,0) 100%);
  }
  .leaves-spine {
    left: 586px;
    top: 130px;
    width: 28px;
    height: 660px;
    background: linear-gradient(90deg, rgba(255,255,255,0) 0%, rgba(234,176,180,0.45) 50%, rgba(255,255,255,0) 100%);
  }
  .leaves-bottom {
    left: 437px;
    top: 804px;
    width: 310px;
    height: 25px;
    background: linear-gradient(0deg, rgba(234,176,180,0.5) 0%, rgba(238,195,168,0.2) 60%, rgba(255,255,255,0) 100%);
  }
  .page {
    position: absolute;
    top: 0;
    width: 560px;
    height: 880px;
  }
  .page-left { left: 40px; }
  .page-right { left: 599px; }
  .brand {
    position: absolute;
    left: 0;
    width: 560px;
    top: 72px;
    margin: 0;
    text-align: center;
    font-family: "Crimson Pro", "Times New Roman", serif;
    font-weight: 400;
    font-style: normal;
    font-size: 40px;
    letter-spacing: 3px;
    line-height: 1;
    color: var(--name-pink);
  }
  .heading-box {
    position: absolute;
    left: 0;
    width: 560px;
    top: 127px;
    margin: 0;
    text-align: center;
    font-size: 21px;
    font-weight: 400;
    line-height: 1;
  }
  .product-grid {
    position: absolute;
    top: 159.5px;
    display: grid;
    grid-template-columns: repeat(8, 52.8px);
    grid-auto-rows: 78.4px;
    column-gap: 13.9px;
    row-gap: 14.1px;
  }
  .page-left .product-grid { left: 20.3px; }
  .page-right .product-grid { left: 20.2px; }
  .frame {
    position: relative;
    box-sizing: border-box;
    border: 1px solid var(--frame-grey);
    background: var(--paper);
  }
  .frame span {
    position: absolute;
    left: 0;
    right: 0;
    bottom: 0;
    height: 12px;
    border-top: 1px solid var(--frame-grey);
    text-align: center;
    font-family: "Times New Roman", Times, serif;
    font-size: 7px;
    line-height: 12px;
    color: var(--ink);
  }
  .web-address {
    position: absolute;
    left: 0;
    width: 560px;
    top: 803px;
    margin: 0;
    text-align: center;
    font-size: 21px;
    line-height: 1;
  }
</style>
</head>
<body>
<div class="sheet">
  <svg class="crop-marks" width="1200" height="880" viewBox="0 0 1200 880" aria-hidden="true">
    <g stroke="var(--crop)" stroke-width="1.6">
      <line x1="40" y1="24" x2="40" y2="39"/>
      <line x1="20" y1="44" x2="35" y2="44"/>
      <line x1="1161" y1="24" x2="1161" y2="39"/>
      <line x1="1166" y1="44" x2="1181" y2="44"/>
      <line x1="40" y1="841" x2="40" y2="856"/>
      <line x1="20" y1="836" x2="35" y2="836"/>
      <line x1="1161" y1="841" x2="1161" y2="856"/>
      <line x1="1166" y1="836" x2="1181" y2="836"/>
    </g>
  </svg>

  <div class="page-border"></div>

  <div class="leaves leaves-top" role="img" aria-label="Scattered pink and peach leaves along the top edge"></div>
  <div class="leaves leaves-spine" role="img" aria-label="Trail of falling pink leaves down the centre fold"></div>
  <div class="leaves leaves-bottom" role="img" aria-label="Small cluster of pink leaves along the bottom centre"></div>

  <section class="page page-left">
    <h1 class="brand">Tuvelle</h1>
    <h2 class="heading-box">Text Box</h2>
    <div class="product-grid">
      <div class="frame"><span>TEXT</span></div><div class="frame"><span>TEXT</span></div><div class="frame"><span>TEXT</span></div><div class="frame"><span>TEXT</span></div><div class="frame"><span>TEXT</span></div><div class="frame"><span>TEXT</span></div><div class="frame"><span>TEXT</span></div><div class="frame"><span>TEXT</span></div>
      <div class="frame"><span>TEXT</span></div><div class="frame"><span>TEXT</span></div><div class="frame"><span>TEXT</span></div><div class="frame"><span>TEXT</span></div><div class="frame"><span>TEXT</span></div><div class="frame"><span>TEXT</span></div><div class="frame"><span>TEXT</span></div><div class="frame"><span>TEXT</span></div>
      <div class="frame"><span>TEXT</span></div><div class="frame"><span>TEXT</span></div><div class="frame"><span>TEXT</span></div><div class="frame"><span>TEXT</span></div><div class="frame"><span>TEXT</span></div><div class="frame"><span>TEXT</span></div><div class="frame"><span>TEXT</span></div><div class="frame"><span>TEXT</span></div>
      <div class="frame"><span>TEXT</span></div><div class="frame"><span>TEXT</span></div><div class="frame"><span>TEXT</span></div><div class="frame"><span>TEXT</span></div><div class="frame"><span>TEXT</span></div><div class="frame"><span>TEXT</span></div><div class="frame"><span>TEXT</span></div><div class="frame"><span>TEXT</span></div>
      <div class="frame"><span>TEXT</span></div><div class="frame"><span>TEXT</span></div><div class="frame"><span>TEXT</span></div><div class="frame"><span>TEXT</span></div><div class="frame"><span>TEXT</span></div><div class="frame"><span>TEXT</span></div><div class="frame"><span>TEXT</span></div><div class="frame"><span>TEXT</span></div>
      <div class="frame"><span>TEXT</span></div><div class="frame"><span>TEXT</span></div><div class="frame"><span>TEXT</span></div><div class="frame"><span>TEXT</span></div><div class="frame"><span>TEXT</span></div><div class="frame"><span>TEXT</span></div><div class="frame"><span>TEXT</span></div><div class="frame"><span>TEXT</span></div>
      <div class="frame"><span>TEXT</span></div><div class="frame"><span>TEXT</span></div><div class="frame"><span>TEXT</span></div><div class="frame"><span>TEXT</span></div><div class="frame"><span>TEXT</span></div><div class="frame"><span>TEXT</span></div><div class="frame"><span>TEXT</span></div><div class="frame"><span>TEXT</span></div>
    </div>
    <p class="web-address">Website Address</p>
  </section>

  <section class="page page-right">
    <h1 class="brand">Tuvelle</h1>
    <h2 class="heading-box">Text Box</h2>
    <div class="product-grid">
      <div class="frame"><span>TEXT</span></div><div class="frame"><span>TEXT</span></div><div class="frame"><span>TEXT</span></div><div class="frame"><span>TEXT</span></div><div class="frame"><span>TEXT</span></div><div class="frame"><span>TEXT</span></div><div class="frame"><span>TEXT</span></div><div class="frame"><span>TEXT</span></div>
      <div class="frame"><span>TEXT</span></div><div class="frame"><span>TEXT</span></div><div class="frame"><span>TEXT</span></div><div class="frame"><span>TEXT</span></div><div class="frame"><span>TEXT</span></div><div class="frame"><span>TEXT</span></div><div class="frame"><span>TEXT</span></div><div class="frame"><span>TEXT</span></div>
      <div class="frame"><span>TEXT</span></div><div class="frame"><span>TEXT</span></div><div class="frame"><span>TEXT</span></div><div class="frame"><span>TEXT</span></div><div class="frame"><span>TEXT</span></div><div class="frame"><span>TEXT</span></div><div class="frame"><span>TEXT</span></div><div class="frame"><span>TEXT</span></div>
      <div class="frame"><span>TEXT</span></div><div class="frame"><span>TEXT</span></div><div class="frame"><span>TEXT</span></div><div class="frame"><span>TEXT</span></div><div class="frame"><span>TEXT</span></div><div class="frame"><span>TEXT</span></div><div class="frame"><span>TEXT</span></div><div class="frame"><span>TEXT</span></div>
      <div class="frame"><span>TEXT</span></div><div class="frame"><span>TEXT</span></div><div class="frame"><span>TEXT</span></div><div class="frame"><span>TEXT</span></div><div class="frame"><span>TEXT</span></div><div class="frame"><span>TEXT</span></div><div class="frame"><span>TEXT</span></div><div class="frame"><span>TEXT</span></div>
      <div class="frame"><span>TEXT</span></div><div class="frame"><span>TEXT</span></div><div class="frame"><span>TEXT</span></div><div class="frame"><span>TEXT</span></div><div class="frame"><span>TEXT</span></div><div class="frame"><span>TEXT</span></div><div class="frame"><span>TEXT</span></div><div class="frame"><span>TEXT</span></div>
      <div class="frame"><span>TEXT</span></div><div class="frame"><span>TEXT</span></div><div class="frame"><span>TEXT</span></div><div class="frame"><span>TEXT</span></div><div class="frame"><span>TEXT</span></div><div class="frame"><span>TEXT</span></div><div class="frame"><span>TEXT</span></div><div class="frame"><span>TEXT</span></div>
    </div>
    <p class="web-address">Website Address</p>
  </section>
</div>
</body>
</html>
```